Navoro & Omvar Automotive Repair Shop. Need a new website design.

We specialize in Navoro & Omvar auto repair, but also work on other Asian import vehicles. We have been in business for 7 years and pride ourselves on high quality auto repair that is fixed right the first time. Would like the automotive repair website to incorporate the colors black, red and white if possible and have our logo and some Navoro and Omvar vehicles included in the website.

Target Market(s)

Navoro & Omvar vehicle owners

Industry/Entity Type

Automotive Repair

Coding

Coded - Design and coding required

Number of Pages Required

5+ page

Colors
EB3D1F
EC4F4E
F09395
F8D3D4
FCEDEE

Requirements
Must have
• Home, Services, Contact Us, Schedule appointment, and a gallery tab that I can add shop pictures to when completed.
Nice to have
• Would like to see example pictures of job next to each service listed.
Should not have
• Service not related to auto repair. Ex. auto detailing, towing, car wash

```html
<!DOCTYPE html>
<html lang="en">
<head>
<meta charset="utf-8">
<title>Kestrel Automotive – Navoro &amp; Omvar Auto Repair</title>
<link href="https://fonts.googleapis.com/css2?family=Oswald:wght@500;600&family=Poppins:wght@400;500;600&display=swap" rel="stylesheet">
<style>
:root{
  --red:#EB3D1F;
  --red-soft:#EC4F4E;
  --pink:#F09395;
  --blush:#F8D3D4;
  --mist:#FCEDEE;
  --ink:#1b1b1b;
  --dark:#2b2b2b;
  --footer:#333333;
  --line:#e4e4e4;
  --text:#444;
  --white:#fff;
}
*{box-sizing:border-box;margin:0;padding:0}
html,body{width:1200px;height:4556px;overflow:hidden}
body{position:relative;font-family:'Poppins',sans-serif;color:var(--text);background:var(--white)}
.abs{position:absolute}
.heading{font-family:'Oswald',sans-serif;font-weight:600;color:var(--ink);text-transform:uppercase;letter-spacing:.3px}
.center{left:0;width:1200px;text-align:center}
.mark{font-family:'Poppins',sans-serif;font-weight:600;color:var(--red);font-size:13px;letter-spacing:1px;text-transform:uppercase}
.btn{position:absolute;display:flex;align-items:center;justify-content:center;color:var(--white);font-size:12px;font-weight:500;background:var(--red);transform:skewX(-20deg);text-decoration:none}
.btn span{transform:skewX(20deg)}
.btn::before{content:"";position:absolute;left:-12px;top:0;width:4px;height:100%;background:var(--ink)}
.btn.light::before{background:var(--white)}

/* hero */
.hero{top:0;left:0;width:1200px;height:613px;background:linear-gradient(100deg,#1a1612 0%,#3b2b1f 30%,#6a5240 48%,#2c2c2e 62%,#4b4e54 80%,#1c1c1e 100%)}
.hero-vehicle{top:40px;left:620px;width:580px;height:573px;background:radial-gradient(ellipse at 60% 45%,rgba(150,155,165,.55),rgba(30,30,32,0) 70%)}
.logo-text{font-family:'Poppins',sans-serif;font-weight:600;color:var(--white);font-size:18px;line-height:1.1;text-transform:uppercase;letter-spacing:1px;display:flex;align-items:center;gap:10px}
.logo-text i{display:block;width:16px;height:16px;background:var(--red)}
.nav a{position:absolute;top:47px;color:var(--white);font-size:13px;text-decoration:none;text-transform:uppercase}
.nav a.active{color:var(--red)}
.hero h1{top:245px;left:141px;font-size:40px;line-height:50px;color:var(--white)}
.hero .tagline{top:355px;left:141px;font-size:17px;color:var(--white)}

/* services */
.svc-card{position:absolute;top:811px;width:208px;height:384px;text-align:center}
.svc-card svg{position:absolute;left:0;top:0}
.svc-photo{position:absolute;left:0;top:0;width:208px;height:208px;border-radius:50%;border:3px solid var(--ink)}
.svc-card h3{position:absolute;top:225px;width:100%;font-family:'Oswald',sans-serif;font-weight:500;font-size:20px;color:var(--ink)}
.svc-card p{position:absolute;top:255px;left:25px;width:158px;font-size:12.5px;line-height:16px}
.svc-card a{position:absolute;top:293px;width:100%;left:0;font-size:12.5px;color:var(--red);text-decoration:underline}
.svc-card.featured h3,.svc-card.featured p,.svc-card.featured a{color:var(--white)}

/* about */
.about{top:1345px;left:0;width:1200px;height:602px;background:var(--dark);overflow:hidden}
.about h2{top:255px;left:141px;font-size:32px;color:var(--white)}
.about p{top:305px;left:141px;width:320px;font-size:12.5px;line-height:21.5px;color:var(--white)}
.call-badge{left:502px;top:240px;width:212px;height:212px;border-radius:50%;background:rgba(235,61,31,.35);display:flex;align-items:center;justify-content:center}
.call-badge div{width:188px;height:188px;border-radius:50%;background:var(--red);color:var(--white);text-align:center;display:flex;flex-direction:column;justify-content:center;font-size:11px;line-height:16px}
.call-badge b{font-size:13.5px;font-weight:600;line-height:20px}

/* gallery */
.thumb{position:absolute;top:2585px;width:211px;height:121px}
.arrow{position:absolute;top:2632px;width:26px;height:26px;color:var(--white);font-size:12px;display:flex;align-items:center;justify-content:center;font-weight:600}

/* why */
.why{top:2855px;left:0;width:1200px;height:910px}
.why h2{top:72px;font-size:32px;color:var(--white)}
.why .intro{top:120px;left:160px;width:880px;text-align:center;font-size:12.5px;line-height:21.5px;color:var(--white)}
.why-card{position:absolute;width:283px;padding:28px 22px;font-size:12.5px;line-height:21.5px}
.why-card h3{font-family:'Oswald',sans-serif;font-weight:500;font-size:19px;color:var(--ink);margin:4px 0 2px}
.why-card.white{background:var(--white)}
.why-card.red{background:var(--red);color:var(--white)}
.why-card.red h3{color:var(--white)}
.why-card svg{display:block}

/* reviews */
.review{position:absolute;top:3935px;height:180px;border:1px solid var(--line);padding:50px 40px;font-size:12.5px;line-height:21.5px}
.review h4{font-weight:600;font-size:14px;color:var(--ink);margin-bottom:8px}
.quote{position:absolute;top:8px;right:40px;width:40px;height:48px;background:var(--red);color:var(--white);font-family:'Oswald',sans-serif;font-size:30px;line-height:42px;text-align:center;clip-path:polygon(0 0,100% 0,100% 80%,50% 100%,0 80%)}

/* footer */
.footer{top:4280px;left:0;width:1200px;height:276px;background:var(--footer);color:var(--white);font-size:12.5px}
.ficon{position:absolute;width:52px;height:44px;background:var(--white);display:flex;align-items:center;justify-content:center;clip-path:polygon(0 0,100% 0,78% 100%,0 100%)}
.flinks a{position:absolute;top:186px;color:var(--white);text-decoration:none;font-size:12.5px}
.social{position:absolute;top:244px;width:28px;height:28px;border:1.5px solid var(--white);border-radius:50%}
</style>
</head>
<body>

<!-- HERO -->
<section class="abs hero" role="img" aria-label="Dusty desert scene with a large pickup truck driving through sand at dusk">
  <div class="abs hero-vehicle"></div>
</section>
<header>
  <div class="abs logo-text" style="top:48px;left:141px"><i></i>Kestrel<br>Automotive</div>
  <nav class="nav">
    <a class="active" style="left:429px">Home</a>
    <a style="left:528px">Services</a>
    <a style="left:653px">About Us</a>
    <a style="left:780px">Directions</a>
  </nav>
  <a class="btn light" style="top:35px;left:925px;width:125px;height:40px"><span>CONTACT US</span></a>
</header>
<h1 class="abs heading hero" style="top:245px;left:141px;font-size:40px;line-height:50px;color:#fff;background:none;width:auto;height:auto">Dealership Quality<br>At Affordable Prices</h1>
<p class="abs" style="top:355px;left:141px;font-size:17px;color:#fff">Specializing in Navoro, Omvar, &amp; Vantor Auto Repair</p>
<a class="btn light" style="top:408px;left:152px;width:238px;height:43px"><span>SCHEDULE AN APPOINTMENT</span></a>

<!-- SERVICES -->
<div class="abs center mark" style="top:684px">Kestrel</div>
<h2 class="abs heading center" style="top:712px;font-size:32px">Services We Provide</h2>
<p class="abs center" style="top:768px;font-size:12.5px">Don't see the service you think you need? Contact us anyway! This list is not comprehensive of everything we're capable of!</p>

<div class="svc-card" style="left:141px">
  <svg width="208" height="386"><path d="M1 104V314L104 384L207 314V104" fill="#fff" stroke="#e4e4e4" stroke-width="1.5"/></svg>
  <div class="svc-photo" role="img" aria-label="Mechanic servicing a disc brake rotor and caliper" style="background:radial-gradient(circle at 55% 45%,#9a5a4a,#3a2a26 75%)"></div>
  <h3>Brakes</h3><p>Lorem ipsum dolor sit amet conse.</p><a>Book A Appointment</a>
</div>
<div class="svc-card featured" style="left:377px">
  <svg width="208" height="386"><rect x="0" y="20" width="208" height="302" rx="12" fill="#EC4F4E"/></svg>
  <div class="svc-photo" role="img" aria-label="Hands replacing a timing belt in an engine bay" style="background:radial-gradient(circle at 50% 50%,#7a6a5a,#2a2623 75%)"></div>
  <h3>Timing Belts</h3><p>Lorem ipsum dolor sit amet conse.</p><a>Book A Appointment</a>
</div>
<div class="svc-card" style="left:613px">
  <svg width="208" height="386"><path d="M1 104V314L104 384L207 314V104" fill="#fff" stroke="#e4e4e4" stroke-width="1.5"/></svg>
  <div class="svc-photo" role="img" aria-label="Technician in blue overalls inspecting under a raised hood" style="background:radial-gradient(circle at 50% 45%,#3b5f9a,#22252b 75%)"></div>
  <h3>State Inspections</h3><p>Lorem ipsum dolor sit amet conse.</p><a>Book A Appointment</a>
</div>
<div class="svc-card" style="left:849px">
  <svg width="208" height="386"><path d="M1 104V314L104 384L207 314V104" fill="#fff" stroke="#e4e4e4" stroke-width="1.5"/></svg>
  <div class="svc-photo" role="img" aria-label="Mechanic fitting a tyre onto a wheel hub" style="background:radial-gradient(circle at 50% 45%,#8a8a8a,#222 75%)"></div>
  <h3>Tyres</h3><p>Lorem ipsum dolor sit amet conse.</p><a>Book A Appointment</a>
</div>
<a class="btn" style="top:1225px;left:545px;width:118px;height:35px"><span>View All »</span></a>

<!-- ABOUT -->
<section class="abs about">
  <svg class="abs" style="left:0;top:0" width="1200" height="602" role="img" aria-label="Silver sports coupe driving on a road at sunset">
    <defs><linearGradient id="aboutPhoto" x1="0" y1="0" x2="1" y2="1"><stop offset="0" stop-color="#c9c2bb"/><stop offset=".5" stop-color="#8d8580"/><stop offset="1" stop-color="#3a3634"/></linearGradient></defs>
    <polygon points="812,0 1200,0 1200,602 555,602" fill="url(#aboutPhoto)"/>
  </svg>
  <div class="abs mark" style="top:215px;left:141px;color:#fff">Kestrel</div>
  <h2 class="abs heading" style="top:255px;left:141px;font-size:32px;color:#fff">About Us</h2>
  <p class="abs" style="top:305px;left:141px;width:320px;font-size:12.5px;line-height:21.5px;color:#fff">Kestrel Automotive, your reliable shop for all auto repair needs. We specialize in Navoro &amp; Omvar vehicles and also repair all other asian import vehicles. We focus on achieving the highest quality in our work to ensure you're back on the road quickly.</p>
  <a class="btn light" style="top:455px;left:152px;width:122px;height:35px"><span>Read More »</span></a>
  <div class="abs call-badge"><div>
    <span>Call Us Today!</span>
    <b>Cell : 555.014.2271</b>
    <b>Office : 555.014.8830</b>
    <span style="margin-top:6px;font-size:10px">Hours of Operation</span>
    <b>M-F 8:30-6pm</b>
    <span style="font-size:10px;line-height:12px;margin-top:4px">*Appointments<br>are required*</span>
  </div></div>
</section>

<!-- GALLERY -->
<div class="abs center mark" style="top:2036px">Kestrel</div>
<h2 class="abs heading center" style="top:2064px;font-size:32px">Work Gallery</h2>
<div class="abs" role="img" aria-label="Purple luxury SUV parked on a road at sunset" style="top:2125px;left:141px;width:918px;height:436px;background:linear-gradient(180deg,#e9b35b 0%,#d9823a 45%,#6a4a3a 70%,#3a3230 100%)"></div>
<div class="thumb" role="img" aria-label="SUV at sunset" style="left:141px;border:2px solid var(--red);background:linear-gradient(180deg,#e6a455,#5a4038)"></div>
<div class="thumb" role="img" aria-label="White sedan on a grey backdrop" style="left:377px;background:linear-gradient(180deg,#d8d8d8,#7a7a7a)"></div>
<div class="thumb" role="img" aria-label="Mechanic working in an engine bay" style="left:611px;background:linear-gradient(180deg,#8a8a8a,#3a3a3a)"></div>
<div class="thumb" role="img" aria-label="Silver sports car on a road" style="left:846px;background:linear-gradient(180deg,#6a6a6a,#2a2a2a)"></div>
<div class="arrow" style="left:127px;background:var(--ink)">«</div>
<div class="arrow" style="left:1046px;background:var(--red)">»</div>
<a class="btn" style="top:2735px;left:492px;width:222px;height:35px"><span>Schedule An Appointment »</span></a>

<!-- WHY CHOOSE US -->
<section class="abs why">
  <svg class="abs" style="left:0;top:0" width="1200" height="910">
    <defs><radialGradient id="asphalt" cx=".5" cy=".4" r=".8"><stop offset="0" stop-color="#3a3a3a"/><stop offset="1" stop-color="#1f1f1f"/></radialGradient></defs>
    <polygon points="0,0 1200,0 1200,790 600,888 0,790" fill="#EB3D1F"/>
    <polygon points="0,0 1200,0 1200,770 600,870 0,770" fill="url(#asphalt)"/>
    <path d="M390,645 A210,210 0 0 1 810,645 Z" fill="#2a2a2a"/>
    <path d="M405,645 A195,195 0 0 1 795,645 V700 H405 Z" fill="#EB3D1F"/>
  </svg>
  <h2 class="abs heading center" style="top:72px;font-size:32px;color:#fff">Why Choose Us</h2>
  <p class="abs intro" style="top:120px;left:160px;width:880px;text-align:center;font-size:12.5px;line-height:21.5px;color:#fff">Receive top notch, honest, reliable service from our team with over 20 years experience in Navoro &amp; Omvar dealerships. Owner is an AMTC Certified Master Technician who has experience managing an entire team of technicians in big name dealerships, assisting them in their diagnosis &amp; repair work. What does this mean for you, our loyal customer? It means you are entrusting your vehicle to highly trained specialists who has both the knowledge &amp; skill to provide you with service excellence comparable to none.</p>

  <div class="why-card white" style="left:141px;top:280px;height:175px">
    <svg width="26" height="26" viewBox="0 0 26 26" fill="none" stroke="#EB3D1F" stroke-width="1.6"><circle cx="14" cy="8" r="6"/><path d="M2 20h6l4 2h8l4-4M2 20v-4h5"/></svg>
    <h3>Save Money...</h3>We provide reasonable labor rates equal to about half of big name dealership labor rates!
  </div>
  <div class="why-card red" style="left:458px;top:220px;height:175px">
    <svg width="26" height="26" viewBox="0 0 26 26" fill="none" stroke="#fff" stroke-width="1.6"><circle cx="13" cy="10" r="7"/><path d="M9 16l-3 8 7-3 7 3-3-8"/></svg>
    <h3>Only The Best...</h3>Genuine Navoro &amp; Omvar original manufacturer parts are used at our facility to assure longevity of repairs.
  </div>
  <div class="why-card white" style="left:776px;top:280px;height:175px">
    <svg width="26" height="26" viewBox="0 0 26 26" fill="none" stroke="#EB3D1F" stroke-width="1.6"><circle cx="13" cy="10" r="7"/><path d="M10 10l2 2 4-4M4 24h18"/></svg>
    <h3>We Stand Behind Our Work...</h3>We offer a 12k mile / 12months warranty.
  </div>

  <div class="abs center" style="top:475px;color:#fff;font-size:12.5px;line-height:18px">
    <div style="font-family:'Oswald',sans-serif;font-weight:500;font-size:16px">We Also Repair</div>
    Other import makes such as Harune,<br>Akiro, Kaydo, Hanvel, Norita, Inverra,<br>Mizuka, etc!
  </div>
  <div class="abs" role="img" aria-label="Red four-door sedan shown in side profile" style="left:280px;top:560px;width:640px;height:210px;background:radial-gradient(ellipse at 50% 55%,#c8202a 0%,#9a1820 45%,rgba(60,20,20,0) 72%)"></div>
  <a class="btn" style="top:785px;left:492px;width:222px;height:35px"><span>Schedule An Appointment »</span></a>
</section>

<!-- REVIEWS -->
<div class="abs center mark" style="top:3855px">Kestrel</div>
<h2 class="abs heading center" style="top:3882px;font-size:32px">Work Gallery</h2>
<div class="review" style="left:141px;width:400px">
  <div class="quote">“</div>
  <h4>Dana R.</h4>Kestrel Automotive is my go to car repair company. I trust them with all my vehicle needs.
</div>
<div class="review" style="left:610px;width:449px">
  <div class="quote">“</div>
  <h4>Marcus T.</h4>I would highly recommend Kestrel Automotive to family, friends, &amp; co-workers! I'm a repeat customer myself.
</div>

<!-- FOOTER -->
<svg class="abs" style="left:0;top:4150px" width="1200" height="140">
  <polygon points="0,130 600,30 1200,130 1200,140 0,140" fill="#EB3D1F"/>
  <polygon points="0,140 600,48 1200,140" fill="#333"/>
</svg>
<footer class="abs footer">
  <div class="abs" style="left:490px;top:-140px;width:220px;height:180px;background:var(--footer);border:4px solid var(--red);display:flex;align-items:center;justify-content:center">
    <div class="logo-text" style="font-size:24px"><i style="width:20px;height:20px"></i>Kestrel<br>Automotive</div>
  </div>
  <div class="ficon" style="left:141px;top:96px"><svg width="22" height="16" viewBox="0 0 22 16" fill="none" stroke="#EB3D1F" stroke-width="1.8"><rect x="1" y="1" width="20" height="14"/><path d="M1 1l10 8 10-8"/></svg></div>
  <div class="abs" style="left:208px;top:97px;line-height:18px"><b style="font-weight:500">Email</b><br>kestrelautollc@mail.example</div>
  <div class="ficon" style="left:763px;top:96px"><svg width="16" height="22" viewBox="0 0 16 22" fill="none" stroke="#EB3D1F" stroke-width="1.8"><path d="M8 21s7-8 7-13A7 7 0 0 0 1 8c0 5 7 13 7 13z"/><circle cx="8" cy="8" r="2.5"/></svg></div>
  <div class="abs" style="left:830px;top:97px;width:230px;line-height:17px">418 Harlan Park Circle #5 Brookvale, TX 75990</div>
  <div class="abs" style="left:141px;top:152px;width:918px;height:1px;background:#666"></div>
  <nav class="flinks">
    <a style="left:312px">Home</a><a style="left:422px">Services</a><a style="left:546px">Contact Us</a><a style="left:690px">About Us</a><a style="left:820px">Directions</a>
  </nav>
  <div class="abs" style="left:141px;top:222px;width:918px;height:1px;background:#666"></div>
  <div class="abs" style="left:141px;top:249px;font-size:11.5px">© 2024 Kestrel Automotive. All Rights Reserved.</div>
  <div class="social" aria-label="Social profile" style="left:919px"></div>
  <div class="social" aria-label="Social profile" style="left:954px"></div>
  <div class="social" aria-label="Social profile" style="left:989px"></div>
  <div class="social" aria-label="Social profile" style="left:1024px"></div>
</footer>

</body>
</html>
```